Magazine Template for National Charity

We need a magazine design for an Australian youth charity called Rhythm Crews Lifting FUtures (RCLF). We engage young people through street culture music, dance and mentoring programs, and help them to turn their lives around. Our charity's vision is to see every young person have someone who believes in them and the opportunity to live their potential.

The design should have places for images of our young people during programs(we've only provided a few for you), room for quotes from young people and supporters etc, and each double spread could be a snapshot of a different program.

We will need a design template that will allow us to add all the contents for the magazine, including a contents page, report from our Chairman (1 page), letter from CEO (1 page), and following achievements of our programs including 1. RCLF Camps (2 x double spread, total 4 pages), 2. Groove Labs (2 x double spread, total 4 pages) and 3. Mentoring (2 x double spread, total 4 pages). An audited financial report of 4 pages will be copied in after our program reports, and on the back of the magazine, we'll need space for all our supporter logos. I'd also like to include a short story or case-study about young people's transformation on each program page.

We need something that's got a bit of a street edge, to keep our youthful brand, but helps us to highlight our excellence as an innovative and cutting edge charity. The final design should be emotional, eye-catching, reflective of our creative spark, and inspiring. We currently have a brand that uses a fair bit of black & white with highlights of colour, however I dont want this to limit your creativity. We use a font called Octin Spraypaint Free for our logos and program names.

We would like to present our annual report as a magazine so that it is something that people will want to pick up and look at.

Target Market(s)

This is for general public and supporters, however we'd like to use our brand instead of a professional style for this report

Industry/Entity Type

Financial

Requirements
Must have
• See notes in task description - thank you!

We will give you a few images to use as a guide however we'd love to be able to play around with the images once we have a template (we'll add different ones and change pictures around to suit the program pages). We're providing these images so that you can get a feel for our culture and be inspired to put together the template, dont worry if you use the same photos more than once on the different pages to show as an example.
Nice to have
• We already have our charity logo, however we'd love to call this RCLF Mag, RCLF Magazine or Newest RCLF Rhythmania. We'd like it to replicate a real magazine, with colour and lots of interesting sections for information & stories, rather than a boring traditional annual report template.
Should not have
• We want this magazine to stand out, and we dont want a half-hearted charity design or a polished corporate style magazine.

We want to remain bold and contemporary, and on the commercial side with a street edge - have lots of fun & thank you so much - we're very excited!

```html
<!DOCTYPE html>
<html lang="en">
<head>
<meta charset="utf-8">
<title>RCLF Magazine – Contents</title>
<link href="https://fonts.googleapis.com/css2?family=Rubik+Dirt&family=Saira+Stencil+One&family=Open+Sans:wght@400;700&display=swap" rel="stylesheet">
<style>
  :root {
    --ink: #1a1a1a;
    --brand-yellow: #f5b21b;
    --paper: #ffffff;
    --muted: #333333;
  }
  * { box-sizing: border-box; margin: 0; padding: 0; }
  html, body { width: 1200px; height: 855px; overflow: hidden; background: var(--paper); }
  .spread {
    position: relative; width: 1200px; height: 855px; background: var(--paper);
    color: var(--ink); font-family: "Open Sans", Arial, sans-serif;
  }
  .headline {
    position: absolute; right: 640px; top: 150px; text-align: right;
    font-family: "Rubik Dirt", Impact, sans-serif; font-size: 52px; line-height: 70.5px;
    letter-spacing: 1px; color: var(--ink); white-space: nowrap;
  }
  .headline .accent { color: var(--brand-yellow); }

  .brand-name {
    position: absolute; right: 58px; top: 14px; text-align: left;
    font-family: "Saira Stencil One", Impact, sans-serif; font-size: 13px; line-height: 14px;
    color: var(--ink); display: flex; align-items: center; gap: 6px;
  }
  .brand-name .mark { width: 10px; height: 26px; background: var(--ink); }

  .contents-badge {
    position: absolute; left: 628px; top: 38px; width: 112px; height: 112px;
    border-radius: 50%; background: var(--brand-yellow);
    display: flex; align-items: center; justify-content: center;
  }
  .contents-badge span {
    font-family: "Saira Stencil One", Impact, sans-serif; color: var(--paper);
    font-size: 20px; transform: rotate(-10deg); letter-spacing: 1px;
  }
  .contents-list {
    position: absolute; left: 632px; top: 160px; list-style: none;
    font-family: "Saira Stencil One", Impact, sans-serif; font-size: 11px; line-height: 19px;
    color: var(--muted); letter-spacing: .5px;
  }

  .info-column { position: absolute; font-size: 9px; line-height: 12px; color: var(--ink); }
  .info-column.purpose { left: 632px; top: 302px; width: 250px; }
  .info-column.people { left: 895px; top: 302px; width: 250px; }
  .info-column h2 { font-size: 10.5px; font-weight: 700; line-height: 14px; }
  .info-column h3 { font-size: 8.5px; font-weight: 700; line-height: 11px; margin-top: 6px; }
  .info-column p { margin-bottom: 12px; }
  .info-column .block { margin-bottom: 10px; }
  .people .entry { margin-bottom: 5px; }
  .people .entry.tight { margin-bottom: 4px; }

  .social {
    position: absolute; left: 632px; top: 779px; display: flex; align-items: center; gap: 10px;
    font-size: 8.5px; line-height: 12px;
  }
  .social .square { width: 22px; height: 22px; background: var(--ink); border-radius: 3px; }
  .social strong { font-weight: 700; }

  .cover-credit { position: absolute; left: 47px; top: 792px; font-size: 7.5px; }
  .cover-credit strong { font-weight: 700; }

  .site-url { position: absolute; left: 1024px; top: 818px; font-size: 10.5px; }
  .page-tab {
    position: absolute; left: 1125px; top: 808px; width: 22px; height: 47px;
    background: var(--brand-yellow); border-radius: 6px 6px 0 0;
    color: var(--paper); font-weight: 700; font-size: 14px; text-align: center; padding-top: 6px;
  }
</style>
</head>
<body>
<main class="spread">

  <h1 class="headline">
    USING THE POWER<br>
    OF MUSIC TO<br>
    <span class="accent">ENGAGE, INSPIRE,</span><br>
    <span class="accent">EDUCATE &amp;</span><br>
    <span class="accent">EMPOWER</span> YOUNG<br>
    PEOPLE
  </h1>

  <div class="brand-name"><span class="mark"></span><span>RHYTHM CREWS LIFTING<br>FUTURES</span></div>

  <div class="contents-badge"><span>CONTENTS</span></div>
  <ol class="contents-list">
    <li>02 A WORD FROM OUR CHAIR</li>
    <li>03 A WORD FROM OUR CEO</li>
    <li>04 STORIES FROM THE RCLF CAMPS</li>
    <li>08 THE GROOVE LABS</li>
    <li>12 RCLF MENTORING</li>
    <li>16 THE NUMBERS</li>
  </ol>

  <section class="info-column purpose">
    <h2>Our Purpose</h2>
    <p>Rhythm Crews Lifting FUtures (RCLF) is a charity that uses the power of music to engage, inspire, educate &amp; empower young people to make their lives remarkable.</p>
    <p>Many young people at RCLF suffer emotionally and socially from traumatic childhood experiences. For them, expressing their pain in lyrics, finding their voice in singing and escaping the world through music has helped them survive.</p>
    <p>Through music, RCLF is able to reach the unreachable, break down social barriers, build self-worth, heal emotional trauma, and transform negative experiences into opportunities to make a difference.</p>
    <h2>Our Belief</h2>
    <p>Every young person deserves to have someone who believes them and the opportunity live their full potential.</p>
    <h2>Contact RCLF</h2>
    <div class="block"><strong>p</strong> 00 0000 0000<br><strong>e</strong> info@rclf.org.au</div>
    <h3>Office</h3>
    <div class="block">Address<br>Address<br>Address</div>
    <h3>Postal Address</h3>
    <div class="block">Address<br>Address</div>
  </section>

  <section class="info-column people">
    <h2>Our People</h2>
    <h3>The Board</h3>
    <div class="entry">board@rclf.org.au</div>
    <div class="entry">Professor Martin Hale MD, MB BS, MRCGP - Chairman</div>
    <div class="entry">Callum Reid – Founder, Director</div>
    <div class="entry">Peter Nolan B.App.Sc.Physiotherapy - Treasurer</div>
    <div class="entry">Sarah Quinlan – Secretary</div>
    <h3>The Heart of RCLF</h3>
    <div class="entry">Callum Reid – CEO<br>callum@rclf.org.au</div>
    <div class="entry">Tessa Reid – Young People &amp; Programs<br>tessa@rclf.org.au</div>
    <div class="entry">Owen Barker – Music Mentor<br>owen@rclf.org.au</div>
    <div class="entry">Lauren Whitfield – Accounts<br>accounts@rclf.org.au</div>
    <div class="entry">Kira Echoes - Music &amp; Youth, Sydney<br>info@rclf.org.au</div>
    <div class="entry">Ben Archer - Music &amp; Youth, Toowoomba<br>info@rclf.org.au</div>
    <div class="entry">Liam Hartley - Music &amp; Youth, Melbourne<br>info@rclf.org.au</div>
    <h3>Our Youngest World Changers</h3>
    <div class="entry tight">Grace Mitchell - Community Events Volunteer<br>events@rclf.org.au</div>
    <div class="entry tight">Noah Jansen – Youth Ambassador<br>volunteers@rclf.org.au</div>
    <div class="entry tight">Lil Jay – Youth Ambassador<br>liljay@rclf.org.au</div>
    <div class="entry tight">Dylan Brooks – Youth Ambassador<br>dylan@rclf.org.au</div>
  </section>

  <div class="social">
    <span class="square" aria-hidden="true"></span>
    <div><strong>join the movement</strong><br>follow us on snapwall, tubestage, chirper</div>
  </div>

  <div class="cover-credit"><strong>Cover Image Credit:</strong> xsdfsdfjksdjkfjkdskfjjsdkjfkkjdsjfksdf</div>

  <div class="site-url">www.rclf.org.au</div>
  <div class="page-tab">1</div>
</main>
</body>
</html>
```